Quorvane Capital LLC

Need Professional Business cards for New Investment Fund

Target Market(s)

High Quality investors

Industry/Entity Type

Financial

Contact Information for Business Card

Phone Number +1 555 284 6190
Name Lukas Varenko
Title Fund Manager
email lv@FundQuorvane.com
Website www.FundQuorvane.com

Colors

Designer to choose colors to be used in the design.

Requirements
Must have
• Must have our Logo and all of the above. Must be made so lettering and loge can be raised

```html
<!DOCTYPE html>
<html lang="en">
<head>
<meta charset="utf-8">
<title>Quorvane Capital LLC — Business Card</title>
<link rel="stylesheet" href="https://fonts.googleapis.com/css2?family=Jost:wght@500;600&family=Roboto:wght@400&display=swap">
<style>
  :root {
    --backdrop: #2a2a2a;
    --card: #171717;
    --wordmark-front: #343434;
    --wordmark-back: #f2f2f2;
    --lime: #8cbf1e;
    --lime-dim: #3d4a2e;
    --text-light: #d6d6d6;
    --text-muted: #6e6e6e;
  }
  * { margin: 0; padding: 0; box-sizing: border-box; }
  html, body {
    width: 1200px;
    height: 1138px;
    overflow: hidden;
    background: var(--backdrop);
  }
  .canvas {
    position: relative;
    width: 1200px;
    height: 1138px;
  }
  .card {
    position: absolute;
    background: var(--card);
    border-radius: 16px;
    overflow: hidden;
  }
  .card--front { left: 274px; top: 186px; width: 622px; height: 374px; }
  .card--back  { left: 276px; top: 608px; width: 618px; height: 374px; }

  .wordmark {
    position: absolute;
    left: 0; right: 0;
    text-align: center;
    font-family: "Jost", sans-serif;
    font-weight: 500;
    letter-spacing: 3px;
    line-height: 1;
    white-space: nowrap;
  }
  .card--front .wordmark {
    top: 164px;
    font-size: 68px;
    color: var(--wordmark-front);
  }
  .card--back .wordmark {
    top: 92px;
    font-size: 52px;
    color: var(--wordmark-back);
  }

  .holder {
    position: absolute;
    left: 0; right: 0;
    top: 212px;
    text-align: center;
  }
  .holder__name {
    font-family: "Jost", sans-serif;
    font-weight: 600;
    font-size: 24px;
    line-height: 1;
    letter-spacing: 1px;
    color: var(--lime);
    text-transform: uppercase;
  }
  .holder__title {
    margin-top: 8px;
    font-family: "Roboto", sans-serif;
    font-size: 16px;
    line-height: 1;
    color: var(--text-light);
  }

  .contacts {
    position: absolute;
    left: 0; right: 0;
    top: 280px;
    font-family: "Roboto", sans-serif;
    font-size: 15px;
    color: var(--text-muted);
  }
  .contacts__row {
    display: flex;
    justify-content: center;
    align-items: center;
    gap: 8px;
    height: 23px;
  }
  .contacts__item {
    display: flex;
    align-items: center;
    gap: 10px;
    white-space: nowrap;
  }
  .contacts__item + .contacts__item { margin-left: 12px; }
  .icon { width: 14px; height: 14px; fill: var(--lime); flex: none; }

  .accent-band {
    position: absolute;
    left: 0; right: 0; bottom: 0;
    height: 15px;
    background: linear-gradient(90deg, var(--lime-dim) 0%, var(--lime) 100%);
  }
</style>
</head>
<body>
<main class="canvas">

  <section class="card card--front" aria-label="Card front">
    <div class="wordmark">QUORVANE</div>
  </section>

  <section class="card card--back" aria-label="Card back">
    <div class="wordmark">QUORVANE</div>

    <div class="holder">
      <p class="holder__name">Lukas Varenko</p>
      <p class="holder__title">Fund Manager</p>
    </div>

    <div class="contacts">
      <div class="contacts__row">
        <span class="contacts__item">
          <svg class="icon" viewBox="0 0 16 16" aria-hidden="true"><path d="M2 6c0-2 2.5-3 6-3s6 1 6 3v1h-3V5.5H5V7H2z M4 8h8l1.5 5h-11z M8 9.2a1.6 1.6 0 1 0 0 3.2a1.6 1.6 0 0 0 0-3.2z"/></svg>
          +1 555 284 6190
        </span>
      </div>
      <div class="contacts__row">
        <span class="contacts__item">
          <svg class="icon" viewBox="0 0 16 16" aria-hidden="true"><path d="M1 3h14v10H1z M2 4.2v.3l6 4.3 6-4.3v-.3z" fill-rule="evenodd"/></svg>
          lv@FundQuorvane.com
        </span>
        <span class="contacts__item">
          <svg class="icon" viewBox="0 0 16 16" aria-hidden="true"><path fill="none" stroke="#8cbf1e" stroke-width="1.4" d="M8 1.5a6.5 6.5 0 1 0 0 13a6.5 6.5 0 0 0 0-13z M1.5 8h13 M8 1.5c-3 3.5-3 9.5 0 13 M8 1.5c3 3.5 3 9.5 0 13 M2.5 4.8h11 M2.5 11.2h11"/></svg>
          www.FundQuorvane.com
        </span>
      </div>
    </div>

    <div class="accent-band"></div>
  </section>

</main>
</body>
</html>
```